Quellbrook Market Counsel needs an email sign off and professional power point template

Newly formed company and we require:1. graphic email signature on our email , and2.a professional powerpoint template (title page and sub pages) and revamp of the attached powerpoint presentation I have uploaded our business car design (logo and contact details ) and a current powerpoint template we are currently working with. Also a brief of how we operateOur mantra is Discover, Develop, Deliver.

Target Market(s)

multinationals and mid size SME's requiring help to grown new markets or geographies for their business.

Colors
000000

Requirements
Must have
• the mantra..our phases of engagement around assisting clients is:
• 1. Discover
• 2. Develop
• 3. Deliver
Nice to have
• we differentiate ourselves form consultant by actually executing the plan for them (i.e. is the delivery phase)

```html
<!DOCTYPE html>
<html lang="en">
<head>
<meta charset="utf-8">
<title>Quellbrook Market Counsel — Email Signature</title>
<link rel="stylesheet" href="https://fonts.googleapis.com/css2?family=Montserrat:wght@400;500;700&display=swap">
<style>
  :root {
    --page: #f3f4f5;
    --navy: #03293b;
    --accent: #1a8fc0;
    --slate: #3a6680;
    --white: #ffffff;
  }
  * { margin: 0; padding: 0; box-sizing: border-box; }
  html, body { width: 1200px; height: 1200px; overflow: hidden; }
  body {
    background: var(--page);
    font-family: "Montserrat", Arial, sans-serif;
    position: relative;
  }
  .signature {
    position: absolute;
    left: 191px; top: 449px;
    width: 819px; height: 216px;
    background: var(--navy);
    overflow: hidden;
  }
  .scenery-left {
    position: absolute; left: 0; top: 0;
    width: 329px; height: 216px;
  }
  .scenery-right {
    position: absolute; left: 713px; top: 127px;
    width: 106px; height: 89px;
  }
  .identity {
    position: absolute; right: 510px; top: 34px;
    text-align: right; line-height: 1;
  }
  .identity__name {
    color: var(--accent);
    font-size: 21px; font-weight: 500;
    letter-spacing: 0.5px; word-spacing: 6px;
  }
  .identity__role {
    color: var(--white);
    font-size: 13px; font-weight: 500;
    margin-top: 6px; letter-spacing: 0.4px;
  }
  .brand {
    position: absolute; left: 369px; top: 70px;
    width: 120px; text-align: center;
    color: var(--white); font-weight: 700;
    font-size: 15px; line-height: 1.25; letter-spacing: 0.5px;
  }
  .brand__mark {
    display: block; width: 12px; height: 12px;
    background: var(--accent); margin: 0 auto 10px;
  }
  .contacts {
    position: absolute; left: 533px; top: 134px;
    list-style: none;
  }
  .contacts__item {
    display: flex; align-items: center;
    height: 20.5px;
    color: var(--white); font-size: 12.5px;
  }
  .contacts__icon { width: 12px; height: 12px; margin-right: 6px; flex: none; }
</style>
</head>
<body>
  <section class="signature" aria-label="Email signature">
    <svg class="scenery-left" role="img" aria-label="Layered blue mountain range illustration" viewBox="0 0 329 216">
      <defs>
        <linearGradient id="scenery-left-fill" x1="0" y1="0" x2="0" y2="1">
          <stop offset="0" stop-color="#03293b"/>
          <stop offset="0.45" stop-color="#2f6483"/>
          <stop offset="1" stop-color="#2a6d92"/>
        </linearGradient>
      </defs>
      <rect width="329" height="216" fill="url(#scenery-left-fill)"/>
    </svg>
    <svg class="scenery-right" role="img" aria-label="Small mountain peaks illustration" viewBox="0 0 106 89">
      <defs>
        <linearGradient id="scenery-right-fill" x1="0" y1="0" x2="0" y2="1">
          <stop offset="0" stop-color="#03293b"/>
          <stop offset="1" stop-color="#1f7ea8"/>
        </linearGradient>
      </defs>
      <rect width="106" height="89" fill="url(#scenery-right-fill)"/>
    </svg>

    <div class="identity">
      <p class="identity__name">NADIA VARGA</p>
      <p class="identity__role">PRINCIPAL</p>
    </div>

    <div class="brand">
      <span class="brand__mark"></span>
      Quellbrook<br>Market Counsel
    </div>

    <ul class="contacts">
      <li class="contacts__item">
        <svg class="contacts__icon" viewBox="0 0 12 12" aria-hidden="true"><path d="M8 1 L6 1 C4 3 3.5 7 5 11 L7 11 L8 9 L6.5 8 C6 6.5 6 4.5 6.7 3.5 L8 3 Z" fill="#1a8fc0"/></svg>
        555-014-2273
      </li>
      <li class="contacts__item">
        <svg class="contacts__icon" viewBox="0 0 12 12" aria-hidden="true"><rect x="0.5" y="2.5" width="11" height="7" fill="#1a8fc0"/><path d="M0.5 2.5 L6 7 L11.5 2.5" fill="none" stroke="#03293b" stroke-width="1"/></svg>
        n.varga@quellbrook.ca
      </li>
      <li class="contacts__item">
        <svg class="contacts__icon" viewBox="0 0 12 12" aria-hidden="true"><circle cx="6" cy="6" r="5.5" fill="#1a8fc0"/><g fill="none" stroke="#03293b" stroke-width="0.8"><ellipse cx="6" cy="6" rx="2.4" ry="5.5"/><path d="M0.5 6 H11.5 M1.5 3.5 H10.5 M1.5 8.5 H10.5"/></g></svg>
        www.quellbrook.ca
      </li>
    </ul>
  </section>
</body>
</html>
```